Birchline Septic Solutions

Would like to see some single sided ones but would also like to see some double sided with one sided only being the logo. Owners name is Colin Vandro. Phone number is 555-214-0387
Services are pumping, inspections, installs, and repairs

Contact Information for Business Card

555-241-0387 Colin Vandro Alder Ridge, OH

```html
<!DOCTYPE html>
<html lang="en">
<head>
<meta charset="utf-8">
<title>Birchline Septic Solutions – Business Card</title>
<link rel="stylesheet" href="https://fonts.googleapis.com/css2?family=Montserrat:wght@500;700;800&display=swap">
<style>
  :root {
    --teal: #2dbcb8;
    --ink: #000000;
    --text: #141414;
    --tagline: #3a3a3a;
    --grey-dark: #c9c9c9;
    --grey-light: #dedede;
    --paper: #ffffff;
    --backdrop: #ececec;
  }
  * { margin: 0; padding: 0; box-sizing: border-box; }
  html, body {
    width: 1093px; height: 1200px; overflow: hidden;
    background: var(--backdrop);
    font-family: "Montserrat", Arial, sans-serif;
  }
  .canvas { position: relative; width: 1093px; height: 1200px; }
  .card {
    position: absolute; left: 264px;
    width: 972px; height: 600px;
    background: var(--paper);
    overflow: hidden;
    transform: scale(0.5957);
    transform-origin: top left;
    box-shadow: 0 2px 6px rgba(0,0,0,0.12);
  }
  .card--front { top: 226px; }
  .card--back { top: 620px; }
  .card__geometry { position: absolute; inset: 0; width: 972px; height: 600px; }

  .brand {
    position: absolute; left: 67px; top: 250px; width: 485px;
    text-align: center; color: var(--ink);
  }
  .brand__name { display: block; font-size: 92px; font-weight: 800; line-height: 1; letter-spacing: 1px; }
  .brand__tagline {
    display: block; margin-top: 26px; color: var(--tagline);
    font-size: 27px; font-weight: 700; letter-spacing: 10px; text-transform: uppercase;
  }

  .contact { position: absolute; left: 64px; top: 98px; color: var(--text); }
  .contact__name { font-size: 37px; font-weight: 800; letter-spacing: 0.5px; text-transform: uppercase; }
  .contact__rows { margin-top: 46px; list-style: none; }
  .contact__row { display: flex; align-items: center; gap: 11px; height: 46px; font-size: 28px; font-weight: 500; letter-spacing: 0.8px; }
  .contact__icon { width: 40px; height: 40px; flex: none; }
  .contact__rule { width: 82px; height: 2px; background: var(--ink); margin-top: 26px; }
  .services { list-style: none; margin-top: 46px; }
  .services__item {
    position: relative; padding-left: 31px; height: 40.5px;
    font-size: 27px; font-weight: 500; letter-spacing: 1px; text-transform: uppercase;
  }
  .services__item::before {
    content: ""; position: absolute; left: 0; top: 6px;
    width: 12px; height: 12px; border-radius: 50%; background: var(--teal);
  }
</style>
</head>
<body>
<main class="canvas">

  <section class="card card--front" aria-label="Card front">
    <svg class="card__geometry" viewBox="0 0 972 600" aria-hidden="true">
      <polygon fill="var(--grey-light)" points="972,0 972,28 400,600 372,600"/>
      <polygon fill="var(--teal)" points="972,70 972,160 532,600 442,600"/>
      <polygon fill="var(--grey-dark)" points="972,200 972,236 608,600 572,600"/>
      <polygon fill="var(--ink)" points="972,270 972,600 642,600"/>
    </svg>
    <div class="brand">
      <span class="brand__name">Birchline</span>
      <span class="brand__tagline">Septic Solutions</span>
    </div>
  </section>

  <section class="card card--back" aria-label="Card back">
    <svg class="card__geometry" viewBox="0 0 972 600" aria-hidden="true">
      <polygon fill="var(--grey-light)" points="972,0 972,28 400,600 372,600"/>
      <polygon fill="var(--teal)" points="972,70 972,160 532,600 442,600"/>
      <polygon fill="var(--grey-dark)" points="972,200 972,236 608,600 572,600"/>
      <polygon fill="var(--ink)" points="972,270 972,600 642,600"/>
    </svg>
    <div class="contact">
      <h1 class="contact__name">Colin Vandro</h1>
      <ul class="contact__rows">
        <li class="contact__row">
          <svg class="contact__icon" viewBox="0 0 40 40" aria-hidden="true">
            <circle cx="20" cy="20" r="20" fill="var(--teal)"/>
            <path d="M13 11.5c1-1 2.2-.8 2.8.2l1.6 2.8c.5.9.2 1.8-.6 2.4l-1 .8c.9 2.3 2.7 4.2 5 5.1l.8-1c.6-.8 1.6-1 2.4-.5l2.8 1.6c1 .6 1.1 1.9.2 2.8l-1.3 1.3c-1.3 1.3-3.3 1.5-5 .6-4.3-2.2-7.6-5.6-9.7-9.9-.8-1.7-.5-3.6.8-4.9z" fill="none" stroke="#fff" stroke-width="1.8" stroke-linejoin="round"/>
            <path d="M22 12.5a6 6 0 0 1 5.5 5.5M22 9a9.5 9.5 0 0 1 9 9" fill="none" stroke="#fff" stroke-width="1.6" stroke-linecap="round"/>
          </svg>
          <span>555-214-0387</span>
        </li>
        <li class="contact__row">
          <svg class="contact__icon" viewBox="0 0 40 40" aria-hidden="true">
            <circle cx="20" cy="20" r="20" fill="var(--teal)"/>
            <path d="M20 9.5a7.5 7.5 0 0 0-7.5 7.5c0 5.3 7.5 13.5 7.5 13.5s7.5-8.2 7.5-13.5A7.5 7.5 0 0 0 20 9.5z" fill="#fff"/>
            <circle cx="20" cy="17" r="2.8" fill="var(--teal)"/>
          </svg>
          <span>Alder Ridge, OH</span>
        </li>
      </ul>
      <div class="contact__rule" role="presentation"></div>
      <ul class="services">
        <li class="services__item">Pumping</li>
        <li class="services__item">Inspections</li>
        <li class="services__item">Installs</li>
        <li class="services__item">Repairs</li>
      </ul>
    </div>
  </section>

</main>
</body>
</html>
```